Simple and Clean business card design

We would like the design to be simple clean and to incorporate our colors.

We are open to your design and talent, we have the dots in our logo as we think of it as data points and we connect data points for people.

We are open to see the great creative and clean design you bring to the table

Contact Information for Business Card

please include: name, position, email, phone and website

Font styles to use
Sans Serif

Requirements
Must have
• my colors incorporated, simplicity
Nice to have
• lots of white space, simplicity
Should not have
• complexicity/ complex art

```html
<!DOCTYPE html>
<html lang="en">
<head>
<meta charset="UTF-8">
<title>Nectra Business Card</title>
<link href="https://fonts.googleapis.com/css2?family=Montserrat:wght@400;500;600&display=swap" rel="stylesheet">
<style>
  :root {
    --bg: #e4e4e4;
    --card-white: #f7f7f7;
    --ink: #111111;
    --text-grey: #444444;
    --brand-blue: #3a6fe0;
    --silver: #bdbdbd;
  }
  * { margin: 0; padding: 0; box-sizing: border-box; }
  html, body { width: 1200px; height: 1200px; overflow: hidden; }
  body {
    background: var(--bg);
    font-family: "Montserrat", sans-serif;
    position: relative;
  }
  .card {
    position: absolute;
    left: 262px;
    width: 686px;
    height: 392px;
    border-radius: 20px;
    overflow: hidden;
  }
  .card-front { top: 165px; background: var(--card-white); }
  .card-back { top: 653px; background: linear-gradient(135deg, #18191b 0%, #2a2b2e 100%); }
  .brand-name {
    position: absolute;
    right: 49px;
    top: 62px;
    font-size: 54px;
    font-weight: 500;
    color: var(--ink);
    letter-spacing: 0.5px;
    line-height: 1;
  }
  .person-name {
    position: absolute;
    left: 54px;
    top: 212px;
    font-size: 22px;
    font-weight: 500;
    color: var(--ink);
    letter-spacing: 0.3px;
  }
  .person-title {
    position: absolute;
    left: 54px;
    top: 240px;
    font-size: 16px;
    color: var(--brand-blue);
  }
  .divider {
    position: absolute;
    left: 56px;
    top: 273px;
    width: 581px;
    height: 1px;
    background: var(--ink);
  }
  .contact-list {
    position: absolute;
    left: 54px;
    top: 290px;
    list-style: none;
  }
  .contact-list li {
    display: flex;
    align-items: center;
    gap: 9px;
    height: 20px;
    font-size: 16px;
    color: var(--text-grey);
  }
  .contact-list svg { width: 13px; height: 13px; flex: none; }
  .base-band {
    position: absolute;
    left: 0;
    bottom: 0;
    width: 100%;
    height: 11px;
    background: var(--brand-blue);
  }
  .back-mark {
    position: absolute;
    inset: 0;
    display: flex;
    align-items: center;
    justify-content: center;
  }
  .back-name {
    font-size: 100px;
    font-weight: 500;
    color: var(--silver);
    line-height: 1;
  }
</style>
</head>
<body>
  <section class="card card-front">
    <div class="brand-name">Nectra</div>

    <h1 class="person-name">DANIEL REYES</h1>
    <p class="person-title">President</p>
    <div class="divider"></div>

    <ul class="contact-list">
      <li>
        <svg viewBox="0 0 24 24"><path fill="var(--brand-blue)" d="M6.6 10.8a15.2 15.2 0 0 0 6.6 6.6l2.2-2.2a1 1 0 0 1 1-.25 11.4 11.4 0 0 0 3.6.57 1 1 0 0 1 1 1V20a1 1 0 0 1-1 1A17 17 0 0 1 3 4a1 1 0 0 1 1-1h3.5a1 1 0 0 1 1 1c0 1.25.2 2.45.57 3.57a1 1 0 0 1-.25 1z"/></svg>
        555-014-2280
      </li>
      <li>
        <svg viewBox="0 0 24 24"><path fill="var(--brand-blue)" d="M2 5h20v14H2z"/><path fill="none" stroke="#fff" stroke-width="2" d="M2 6l10 7 10-7"/></svg>
        hello@nectra.com
      </li>
      <li>
        <svg viewBox="0 0 24 24"><circle cx="12" cy="12" r="10" fill="var(--brand-blue)"/><path fill="none" stroke="#fff" stroke-width="1.6" d="M2 12h20M12 2c3 3 3 17 0 20M12 2c-3 3-3 17 0 20"/></svg>
        nectra.com
      </li>
    </ul>

    <div class="base-band"></div>
  </section>

  <section class="card card-back">
    <div class="back-mark">
      <span class="back-name">Nectra</span>
    </div>
  </section>
</body>
</html>
```